Custom Cabinet Shop Needs a website design

Hi,
We need a website for a Custom Cabinet Shop and Cabinet parts manufacturing business.
The business has two sides to it. One side provides custom Kitchens, vanities, entertainment units, offices and what not to homeowners and contractors.
The 2nd side of the business provides built to order cabinet boxes and other parts required to put together a project to other cabinet shops, small contractors looking to install there own cabinets.
Website will need a Gallery to display work.
Color scheme to go well with logo.
current website is www.brambleoakcustomcabinets.com
being changed to www.brambleoak.ca
Logo Included in attached files.
Tagline "Joinery with Spirit"
Mission Statement "Our passion is to deliver inspired cabinetry solutions to suit all your needs, supported by our phenomenal star class customer service"
The website should convey quality and professionalism.
Thank you.
Homeowners/ Contractors
Entertainment

```html
<!DOCTYPE html>
<html lang="en">
<head>
<meta charset="utf-8">
<title>Brambleoak Custom Cabinets</title>
<link rel="stylesheet" href="https://fonts.googleapis.com/css2?family=Open+Sans:wght@400;600&family=Lato:wght@400;700&family=PT+Sans&family=Kaushan+Script&family=Courier+Prime&display=swap">
<style>
:root{
  --black:#000;
  --orange:#f9633a;
  --accent:#e2411c;
  --red:#d33417;
  --ink:#222;
  --body:#6a6a6a;
  --white:#fff;
  --nav-bg:#fff;
  --search-bg:#e4e4e4;
}
*{box-sizing:border-box;margin:0;padding:0}
html,body{width:1200px;height:2368px;overflow:hidden;background:var(--white)}
body{position:relative;font-family:"PT Sans",sans-serif;color:var(--ink)}
.abs{position:absolute}
.top-bar{left:0;top:0;width:1200px;height:88px;background:var(--black)}
.brand{left:88px;top:24px;display:flex;align-items:center;gap:12px}
.brand-dot{width:40px;height:40px;border-radius:50%;background:var(--accent)}
.brand-name{font-family:"Open Sans",sans-serif;font-weight:600;font-size:24px;color:var(--white);letter-spacing:1px}
.address{left:904px;top:24px;display:flex;gap:14px;font-size:13px;line-height:23px;color:var(--accent)}
.hero{left:0;top:88px;width:1200px;height:612px;background:linear-gradient(180deg,#3c3a3a 0%,#5a4a3c 45%,#3a2a20 100%)}
.nav{left:88px;top:110px;width:1024px;height:59px;background:var(--nav-bg);border-radius:3px;box-shadow:0 2px 4px rgba(0,0,0,.3);display:flex;align-items:center;padding-left:26px}
.nav a{font-family:"Open Sans",sans-serif;font-size:15px;color:var(--ink);text-decoration:none;margin-right:48px}
.search{position:absolute;right:16px;top:15px;width:278px;height:30px;border-radius:4px;background:var(--search-bg);box-shadow:inset 0 1px 2px rgba(0,0,0,.2);font-size:11px;color:#aaa;padding:7px 12px}
.search svg{position:absolute;right:10px;top:7px}
.tagline{left:0;top:352px;width:1200px;text-align:center;font-family:"Kaushan Script",cursive;font-size:92px;color:var(--white);text-shadow:0 2px 6px rgba(0,0,0,.5)}
.arrow{width:46px;height:46px;border-radius:50%;background:var(--red);top:677px;display:flex;align-items:center;justify-content:center}
h2{font-family:"Open Sans",sans-serif;font-weight:400;font-size:31px}
.rule{width:40px;height:4px;background:var(--accent)}
.quote{font-family:"Lato",sans-serif;font-weight:700;font-size:19px;line-height:27px;color:var(--accent)}
.body-text{font-size:13px;line-height:26px;color:var(--body)}
.read-more{left:88px;top:1070px;display:flex;align-items:center;gap:30px;font-family:"Open Sans",sans-serif;font-size:19px}
.feature-photo{left:800px;top:853px;width:304px;height:246px;background:linear-gradient(135deg,#c8c8c8,#2a2a2a 55%,#8a8a8a)}
.services{left:0;top:1153px;width:1200px;height:417px;background:var(--orange)}
.mono-quote{font-family:"Courier Prime",monospace;font-variant:small-caps;letter-spacing:2.5px;font-size:16px;line-height:27px;color:var(--white)}
.card-photo{width:487px;height:204px}
.card-label{width:487px;text-align:center;font-family:"Open Sans",sans-serif;font-size:22px;color:#2a1a14}
.tile{width:325px;height:195px}
.view-all{left:0;top:2170px;width:1200px;display:flex;justify-content:center;align-items:center;gap:10px;font-size:13px;color:var(--accent)}
.footer{left:0;top:2242px;width:1200px;height:126px;background:var(--black)}
.copyright{left:88px;top:2296px;font-family:"Courier Prime",monospace;font-variant:small-caps;letter-spacing:2px;font-size:12px;color:var(--white)}
.social{width:38px;height:38px;border-radius:50%;top:2286px}
</style>
</head>
<body>
<header class="abs top-bar"></header>
<div class="abs brand"><span class="brand-dot"></span><span class="brand-name">BRAMBLEOAK</span></div>
<div class="abs address">
  <svg width="26" height="22" viewBox="0 0 26 22"><path d="M13 1 1 12h4v9h6v-6h4v6h6v-9h4z" fill="#fff"/></svg>
  <div>48210 Range Road 195<br>Cedar Hollow, Alberta, T9Z 4K2</div>
</div>

<div class="abs hero" role="img" aria-label="Photo of a dark basement bar with stone counter, bar stools and pendant lights"></div>
<nav class="abs nav">
  <a>Home</a><a>Gallery</a><a>Services</a><a>Warranty</a><a>Contact</a>
  <div class="search">Search....
    <svg width="16" height="16" viewBox="0 0 16 16"><circle cx="6.5" cy="6.5" r="4.5" fill="none" stroke="#999" stroke-width="1.6"/><path d="M10 10l4 4" stroke="#999" stroke-width="1.8"/></svg>
  </div>
</nav>
<div class="abs tagline">Joinery with Spirit</div>
<div class="abs arrow" style="left:552px"><svg width="14" height="14" viewBox="0 0 14 14"><path d="M9 2 4 7l5 5" fill="none" stroke="#fff" stroke-width="2.4"/></svg></div>
<div class="abs arrow" style="left:601px"><svg width="14" height="14" viewBox="0 0 14 14"><path d="M5 2l5 5-5 5" fill="none" stroke="#fff" stroke-width="2.4"/></svg></div>

<section>
  <h2 class="abs" style="left:88px;top:762px">Welcome</h2>
  <div class="abs rule" style="left:88px;top:814px"></div>
  <p class="abs quote" style="left:88px;top:850px;width:660px">“ Our passion is to deliver inspired cabinetry solutions to suit all your needs, supported by our phenomenal star class customer service ”</p>
  <p class="abs body-text" style="left:88px;top:942px;width:650px">Neque porro quisquam est, qui dolorem ipsum quia dolor sit amet, consectetur, adipisci velit, sed quia non numquam eius modi tempora incidunt ut labore et dolore magnam aliquam quaerat voluptatem. Ut enim ad minima veniam, quis nostrum exercitationem.Neque porro quisquam est, qui dolorem ipsum quia dolor sit amet, consectetur, adipisci velit, sed quia non numquam eius modi tempora.</p>
  <div class="abs read-more">Read More
    <svg width="20" height="20" viewBox="0 0 20 20"><circle cx="10" cy="10" r="10" fill="#111"/><path d="M6 10h7M10 6l4 4-4 4" fill="none" stroke="#fff" stroke-width="2.2"/></svg>
  </div>
  <div class="abs feature-photo" role="img" aria-label="Image of a desktop screen showing a modern black and white kitchen"></div>
</section>

<section class="abs services"></section>
<h2 class="abs" style="left:88px;top:1200px;color:#fff">Services</h2>
<div class="abs rule" style="left:88px;top:1250px;background:#000"></div>
<p class="abs mono-quote" style="left:346px;top:1205px;width:700px">“ We create a bespoke proposal for each and every client, paying attention to those little details that matter ”</p>
<div class="abs card-photo" style="left:88px;top:1295px;background:linear-gradient(135deg,#d8d4cc,#2a2624 60%,#8a7a6a)" role="img" aria-label="Photo of a residential kitchen with dark island"></div>
<div class="abs card-photo" style="left:625px;top:1295px;background:linear-gradient(135deg,#eee,#6a5a50 55%,#3a2e2a)" role="img" aria-label="Photo of an office desk with chair"></div>
<div class="abs card-label" style="left:88px;top:1507px">Residential</div>
<div class="abs card-label" style="left:625px;top:1507px">Business</div>

<section>
  <h2 class="abs" style="left:88px;top:1622px">Gallery</h2>
  <div class="abs rule" style="left:88px;top:1673px"></div>
  <p class="abs quote" style="left:344px;top:1628px;width:720px">“ We are a small, passionate team. We love what we do, and that's what makes our team special. ”</p>
  <div class="abs tile" style="left:88px;top:1727px;background:linear-gradient(#2a2220,#8a8480)" role="img" aria-label="Photo of tall dark cabinetry"></div>
  <div class="abs tile" style="left:437px;top:1727px;background:linear-gradient(#9a8a78,#2a2420)" role="img" aria-label="Photo of kitchen island with granite top"></div>
  <div class="abs tile" style="left:786px;top:1727px;background:linear-gradient(#5a5048,#2a1e18)" role="img" aria-label="Photo of basement bar with stools"></div>
  <div class="abs tile" style="left:88px;top:1948px;background:linear-gradient(#c8c2b8,#2a2420)" role="img" aria-label="Photo of white kitchen with dining table"></div>
  <div class="abs tile" style="left:437px;top:1948px;background:linear-gradient(#d0c8bc,#3a2a24)" role="img" aria-label="Photo of kitchen with large island"></div>
  <div class="abs tile" style="left:786px;top:1948px;background:linear-gradient(#c8c0b4,#3a3030)" role="img" aria-label="Photo of bedroom with dark built-in units and fireplace"></div>
  <div class="abs view-all">
    <svg width="13" height="13" viewBox="0 0 14 14"><circle cx="7" cy="7" r="7" fill="#e2411c"/><path d="M4 5.5 7 8.5 10 5.5" fill="none" stroke="#fff" stroke-width="1.8"/></svg>
    View Full Gallery
  </div>
</section>

<footer class="abs footer"></footer>
<div class="abs copyright">© 2015 Brambleoak Custom Cabinets. All Rights Reserved</div>
<div class="abs social" style="left:879px;background:#2b4a8c"></div>
<div class="abs social" style="left:928px;background:#1a9be0"></div>
<div class="abs social" style="left:977px;background:#c8102e"></div>
<div class="abs social" style="left:1025px;background:#1f8ecb"></div>
<div class="abs social" style="left:1074px;background:#c81e2a"></div>
</body>
</html>
```